Financial Advisor Business Card

This business card is mainly a card for me personally (Marcus Obelwyn) providing services as a Financial Planner and Accountant. My title is: Brightway Mentor
Details provided about Harbourline Financial Advisors on the reverse side of the card is not dominant information, it is provided for ease of contact/communication purposes for prospective clients.
About me: I provide financial advice to my clients however due to regulatory issues in my industry I cannot use the title "Financial Advisor".
Target market is 25 y/o and onwards projecting a cutting edge, innovative and modern marketing influence.
Target Market(s)
25 years old and older
Industry/Entity Type
Financial
Contact Information for Business Card
Front side of business card
Name: Marcus Obelwyn
Position: Brightway Mentor
Accreditations:
Dip FS(FP)
B.Comm
Mobile: 0438 927 583
e-mail: mo@harbourlinefa.com.au
website: www.harbourlinefa.com.au
Reverse side of business card
Name: Marcus Obelwyn
Company: Harbourline Financial Advisors
Position: Senior Accountant
Address:
Level 6, Suite 4
47 Pelham Road
PO Box 718
CHARLESTOWN NSW 2290
Phone: (02) 49718352
Requirements
Must have
- - Cutting edge, innovative, fun but professional, modern marketing design and fonts
- Professional and legible
- Futuristic sharp lines, some with rounded edges
- Preferred Front Card colour scheme: Black background, Silver Text, White Text, Red & Silver lines
- Preferred Reverse Card colour scheme: White background, Silver Text, Black Text, Aqua & Silver lines
Nice to have
- Design a cutting edge logo of my intials as capital letters: MO
with a bigger D and smaller K - Preferred colour is Silver Text
Should not have
- Must not be:
- vintage/classic
- stereotypical accountant/tax agent/money style business card
- old style fonts e.g. times new roman

```html
<!DOCTYPE html>
<html lang="en">
<head>
<meta charset="utf-8">
<title>Marcus Obelwyn – Business Card</title>
<link rel="stylesheet" href="https://fonts.googleapis.com/css2?family=Open+Sans:wght@400;700&display=swap">
<style>
  :root {
    --page: #e9e7e4;
    --card-black: #0b0b0b;
    --red: #b3202a;
    --red-dark: #8a1a20;
    --ink: #3a3a3a;
    --ink-soft: #555555;
    --white: #f2f2f2;
  }
  * { box-sizing: border-box; margin: 0; padding: 0; }
  html, body { width: 1200px; height: 1024px; overflow: hidden; }
  body {
    background: var(--page);
    font-family: "Open Sans", Arial, sans-serif;
    position: relative;
  }
  .card {
    position: absolute;
    width: 700px;
    height: 400px;
    overflow: hidden;
    box-shadow: 0 10px 30px rgba(0,0,0,0.18);
  }

  /* Front card */
  .card-front {
    left: 90px; top: 100px;
    background: linear-gradient(180deg, #ffffff 0%, #f3f3f3 100%);
  }
  .front-band {
    position: absolute; left: 0; right: 0; bottom: 0; height: 28px;
    background: linear-gradient(90deg, var(--red-dark), var(--red) 60%, #c52630);
  }
  .front-band-end {
    position: absolute; right: 0; bottom: 0; width: 70px; height: 28px;
    background: #111;
  }
  .brand-mark {
    position: absolute; display: flex; align-items: center; gap: 14px;
    font-weight: 400; line-height: 1;
  }
  .brand-mark .brand-dot { flex: none; border-radius: 50%; }
  .front-brand { left: 60px; bottom: 90px; font-size: 64px; color: var(--red-dark); }
  .front-brand .brand-dot { width: 18px; height: 18px; background: var(--red-dark); }
  .front-divider {
    position: absolute; left: 330px; top: 96px; width: 2px; height: 150px;
    background: linear-gradient(180deg, rgba(138,26,32,0), var(--red-dark) 40%, rgba(138,26,32,0.2));
  }
  .contact {
    position: absolute; left: 370px; top: 90px;
    color: var(--ink); font-size: 15px; line-height: 1.55;
  }
  .contact-name { color: var(--red-dark); font-weight: 700; font-size: 20px; }
  .contact-title, .contact-creds { color: var(--ink-soft); }
  .contact-line { display: flex; align-items: center; gap: 8px; }
  .contact-line svg { width: 13px; height: 13px; flex: none; }

  /* Back card */
  .card-back {
    left: 410px; top: 540px;
    background: radial-gradient(ellipse at 60% 45%, #1c1c1c 0%, var(--card-black) 70%);
  }
  .back-brand { left: 270px; top: 150px; font-size: 80px; color: var(--red); }
  .back-brand .brand-dot { width: 20px; height: 20px; background: var(--red); }
  .back-web {
    position: absolute; left: 40px; bottom: 34px;
    color: var(--white); font-size: 20px; letter-spacing: 0.5px;
  }
</style>
</head>
<body>
  <section class="card card-front" aria-label="Business card front">
    <div class="brand-mark front-brand"><span class="brand-dot"></span><span>MO</span></div>
    <div class="front-divider"></div>
    <div class="contact">
      <div class="contact-name">Marcus Obelwyn</div>
      <div class="contact-title">Brightway Mentor</div>
      <div class="contact-creds">Dip FS(FP) | B.Comm</div>
      <div class="contact-line">
        <svg viewBox="0 0 12 12" aria-hidden="true"><rect x="2.5" y="0.5" width="7" height="11" rx="1.2" fill="none" stroke="#b3202a" stroke-width="1.2"/></svg>
        <span>0438 927 583</span>
      </div>
      <div class="contact-line">
        <svg viewBox="0 0 12 12" aria-hidden="true"><rect x="0.5" y="2" width="11" height="8" rx="1" fill="#b3202a"/><path d="M1 3 L6 7 L11 3" stroke="#fff" fill="none" stroke-width="1"/></svg>
        <span>mo@harbourlinefa.com.au</span>
      </div>
      <div class="contact-line">
        <svg viewBox="0 0 12 12" aria-hidden="true"><circle cx="6" cy="6" r="5.5" fill="#b3202a"/><path d="M0.5 6 H11.5 M6 0.5 C3 3 3 9 6 11.5 M6 0.5 C9 3 9 9 6 11.5" stroke="#fff" fill="none" stroke-width="0.8"/></svg>
        <span>www.harbourlinefa.com.au</span>
      </div>
    </div>
    <div class="front-band"></div>
    <div class="front-band-end"></div>
  </section>

  <section class="card card-back" aria-label="Business card back">
    <div class="brand-mark back-brand"><span class="brand-dot"></span><span>MO</span></div>
    <div class="back-web">www.harbourlinefa.com.au</div>
  </section>
</body>
</html>
```